ORLA - Óptica Médica - web design and concept

Website concept - Create and develop our website design and structure. ORLA is an optical store chain, and we are looking to establish our web and digital concept. In attachment there are several pictures about our stores and our logo.

The website structure should be user friendly. Colors should be light and the design as simple and minimalist as possible. There are different variations of the logothat can be used, check the file.

The website will include optical collections and sun collections as an online store. Also, a medical menu should be considered in order for clients to schedule optometry appointments. There should also be a menu for client assistance where the clients can read about glass maintenance in our workshop.
Updates

Low design quality

Number of Pages Required

5+ page

Font styles to use
Serif
Sans Serif

Requirements
Must have
• Must be user-friendly and minimalist.
• Please USE PICTURES FROM THE BRANDS we sell: MERUN, BOSKA, PNW, KOLE, BAMPE
Nice to have
• Nice to inspire: ZEK glasses (see website https://ch.shopzek.com/en/)
• Nice to inspire: https://merun-eyewear.com/
• Nice to ispire: https://www.pnwglobe.com/en/
Should not have
• Hysteric colors and shapes

```html
<!DOCTYPE html>
<html lang="en">
<head>
<meta charset="utf-8">
<title>ORLA Óptica Médica</title>
<link href="https://fonts.googleapis.com/css2?family=Cantarell:wght@400;700&family=Cinzel:wght@400;700&family=Open+Sans:wght@400;600;700&display=swap" rel="stylesheet">
<style>
  :root{
    --page:#f7f2ea;
    --header:#ffffff;
    --band:#efe6d8;
    --gold:#c98f1c;
    --frame:#c9a05a;
    --ink:#2b221b;
    --text:#5a4e44;
    --line:#e2d6c3;
    --ghost:rgba(60,40,20,0.06);
    --white:#ffffff;
  }
  *{box-sizing:border-box;margin:0;padding:0}
  html,body{width:1200px;height:3072px;overflow:hidden}
  body{background:var(--page);color:var(--ink);font-family:"Open Sans",Arial,sans-serif;position:relative}
  .abs{position:absolute}

  /* header */
  .site-header{left:0;top:0;width:1200px;height:106px;background:var(--header);border-bottom:1px solid var(--line)}
  .brand-name{left:122px;top:24px;font-family:"Cantarell",sans-serif;font-weight:700;font-size:34px;letter-spacing:4px;color:var(--gold)}
  .cart{right:100px;top:26px;font-size:13px;font-weight:600;display:flex;align-items:center;gap:8px}
  .main-nav{right:86px;top:60px;display:flex;gap:22px;align-items:center;font-size:14px;font-weight:600;white-space:nowrap}
  .main-nav .active{color:var(--gold)}

  /* hero */
  .hero{left:0;top:106px;width:1200px;height:467px;background:linear-gradient(180deg,#cfc4b3 0%,#d9cfbf 30%,#8fb8ba 55%,#d8ccb8 80%,#c4b7a3 100%)}
  .hero-box{left:317px;top:211px;width:568px;height:184px;border:1px solid rgba(255,255,255,0.7);background:rgba(40,34,28,0.45);text-align:center;color:var(--white)}
  .hero-box h1{font-family:"Cantarell",sans-serif;font-weight:400;font-size:47px;margin-top:24px}
  .hero-box p{font-size:20px;line-height:32px;margin-top:8px}
  .dots{left:576px;top:535px;display:flex;gap:4px}
  .dots span{width:10px;height:10px;border-radius:50%;border:1px solid #fff}
  .dots span.on{background:#fff}

  /* sections */
  .ghost{font-family:"Cinzel",serif;font-weight:700;color:var(--ghost);white-space:nowrap}
  .section-title{font-family:"Cantarell",sans-serif;font-weight:400;font-size:35px;width:1200px;left:0;text-align:center}

  .about-ghost{left:86px;top:670px;font-size:82px}
  .about-title{left:209px;top:698px;font-family:"Cantarell",sans-serif;font-weight:400;font-size:35px}
  .about-text{left:571px;top:660px;width:496px;font-size:12.5px;line-height:27px;color:var(--text);text-align:justify}
  .btn-video{left:571px;top:762px;width:127px;height:43px;border:2px solid var(--ink);font-size:14px;font-weight:600;display:flex;align-items:center;justify-content:center}

  .products-ghost{left:0;width:1200px;text-align:center;top:944px;font-size:86px}
  .products-title{top:972px}
  .product{width:232px;top:1081px}
  .product .photo{width:232px;height:211px;border:2px solid var(--line)}
  .product .label{margin-top:12px;text-align:center;font-family:"Cantarell",sans-serif;font-size:15px}
  .arrow{top:1170px}

  .wave{left:0;width:1200px;background:radial-gradient(ellipse 60% 30% at 60% 50%,rgba(214,140,60,0.22),rgba(247,242,234,0) 70%)}

  .guarantees-ghost{left:0;width:1200px;text-align:center;top:1696px;font-size:86px}
  .guarantees-title{top:1724px}
  .guarantee{width:240px;top:1844px;text-align:center}
  .guarantee svg{display:block;margin:0 auto}
  .guarantee h3{margin-top:18px;font-size:15px;line-height:23px;font-weight:700;color:var(--gold)}
  .guarantee p{margin-top:4px;font-size:12px;line-height:23px;color:var(--text)}

  .brands-ghost{left:0;width:1200px;text-align:center;top:2430px;font-size:86px}
  .brands-title{top:2460px}
  .brand-box{top:2578px;width:234px;height:113px;border:3px solid var(--frame);background:var(--white);display:flex;align-items:center;justify-content:center;font-family:"Cantarell",sans-serif;font-weight:700;font-size:25px;letter-spacing:1px}

  /* footer */
  .site-footer{left:0;top:2820px;width:1200px;height:252px;background:var(--band)}
  .footer-name{left:0;width:1200px;text-align:center;top:2884px;font-family:"Cantarell",sans-serif;font-weight:700;font-size:40px;letter-spacing:5px;color:var(--gold)}
  .footer-nav{left:0;width:1200px;top:2983px;display:flex;justify-content:center;gap:21px;font-size:14px;font-weight:600}
  .copyright{left:0;width:1200px;top:3018px;text-align:center;font-size:11px;color:var(--text)}
</style>
</head>
<body>

<header class="site-header abs">
  <div class="brand-name abs">ORLA</div>
  <div class="cart abs">
    <svg width="15" height="13" viewBox="0 0 15 13"><path d="M0 1h3l2 7h8l2-5H4.5" fill="none" stroke="#2b221b" stroke-width="1.6"/><circle cx="6" cy="11" r="1.4" fill="#2b221b"/><circle cx="12" cy="11" r="1.4" fill="#2b221b"/></svg>
    MY CART (0)
  </div>
  <nav class="main-nav abs">
    <span class="active">START</span><span>ABOUT US</span><span>PRODUCTS</span><span>APPOINTMENTS</span><span>ASSISTANCE</span><span>CONTACT</span><span>BLOG</span><span>STORE</span>
    <svg width="14" height="14" viewBox="0 0 14 14"><circle cx="5.8" cy="5.8" r="4.3" fill="none" stroke="#2b221b" stroke-width="2"/><path d="M9 9l4 4" stroke="#2b221b" stroke-width="2.4"/></svg>
  </nav>
</header>

<section class="hero abs" role="img" aria-label="Interior of an ORLA optical store with display walls and counters"></section>
<div class="hero-box abs">
  <h1>ORLA OPTICS</h1>
  <p>Best professionals &amp; the most competitive<br>products to serve your needs</p>
</div>
<div class="dots abs"><span class="on"></span><span></span><span></span><span></span></div>

<div class="ghost about-ghost abs">ABOUT US</div>
<h2 class="about-title abs">ABOUT US</h2>
<p class="about-text abs">Orla Óptica is the dream of a young entrepreneur named Tomás. With a degree in optics and optometry, he has acquired knowledge and skills to provide that multi disciplinary and demanding service that you deserve.</p>
<div class="btn-video abs">Watch Video</div>

<div class="ghost products-ghost abs">OUR PRODUCTS</div>
<h2 class="section-title products-title abs">OUR PRODUCTS</h2>
<svg class="arrow abs" style="left:44px" width="14" height="22" viewBox="0 0 14 22"><path d="M11 3L3 11l8 8" fill="none" stroke="#2b221b" stroke-width="3"/></svg>
<svg class="arrow abs" style="left:1140px" width="14" height="22" viewBox="0 0 14 22"><path d="M3 3l8 8-8 8" fill="none" stroke="#2b221b" stroke-width="3"/></svg>
<div class="product abs" style="left:98px"><div class="photo" role="img" aria-label="Woman wearing graduated glasses frames" style="background:linear-gradient(135deg,#6b4f40,#c49a82 55%,#eee4dc)"></div><div class="label">GRADUATED FRAME</div></div>
<div class="product abs" style="left:354px"><div class="photo" role="img" aria-label="Pair of ophthalmic lenses" style="background:linear-gradient(135deg,#f1efee,#d8d6d5 60%,#f4f3f2)"></div><div class="label">OPHTHALMIC LENSES</div></div>
<div class="product abs" style="left:611px"><div class="photo" role="img" aria-label="Couple wearing sunglasses" style="background:linear-gradient(135deg,#e8b86a,#d39a66 50%,#8cc3cf)"></div><div class="label">SUN GLASSES</div></div>
<div class="product abs" style="left:868px"><div class="photo" role="img" aria-label="Contact lenses and case" style="background:linear-gradient(135deg,#eef2f3,#cfdfe3 55%,#8fd0dc)"></div><div class="label">CONTACT LENSES</div></div>

<div class="wave abs" style="top:1380px;height:270px" role="img" aria-label="Flowing warm light streaks"></div>

<div class="ghost guarantees-ghost abs">OUR GUARANTEES</div>
<h2 class="section-title guarantees-title abs">OUR GUARANTEES</h2>

<div class="guarantee abs" style="left:120px">
  <svg width="119" height="131" viewBox="0 0 119 131"><polygon points="59.5,0 119,33 119,98 59.5,131 0,98 0,33" fill="var(--gold)"/><circle cx="59.5" cy="50" r="6" fill="#fff"/><rect x="51" y="59" width="17" height="20" rx="3" fill="#fff"/><rect x="53" y="76" width="5" height="14" fill="#fff"/><rect x="61" y="76" width="5" height="14" fill="#fff"/></svg>
  <h3>ORLA CHILDHOOD<br>GUARANTEE</h3>
  <p>50% discount on new glasses, if your<br>child's graduation has changed</p>
</div>
<div class="guarantee abs" style="left:359px">
  <svg width="119" height="131" viewBox="0 0 119 131"><polygon points="59.5,0 119,33 119,98 59.5,131 0,98 0,33" fill="var(--gold)"/><rect x="36" y="50" width="34" height="30" rx="2" fill="#fff"/><path d="M70 58h9l7 9v13H70z" fill="#fff"/><rect x="50" y="55" width="6" height="18" fill="var(--gold)"/><rect x="44" y="61" width="18" height="6" fill="var(--gold)"/><circle cx="46" cy="82" r="5" fill="#fff" stroke="var(--gold)" stroke-width="2"/><circle cx="76" cy="82" r="5" fill="#fff" stroke="var(--gold)" stroke-width="2"/></svg>
  <h3>ORLA ACCIDENT<br>WARRANTY</h3>
  <p>50% discount on new glasses, if your<br>child's graduation has changed</p>
</div>
<div class="guarantee abs" style="left:599px">
  <svg width="119" height="131" viewBox="0 0 119 131"><polygon points="59.5,0 119,33 119,98 59.5,131 0,98 0,33" fill="var(--gold)"/><path d="M47 55l4-12h17l4 12z" fill="#fff"/><rect x="41" y="54" width="37" height="4" fill="#fff"/><circle cx="59.5" cy="66" r="9" fill="#fff"/><path d="M42 90c2-10 8-14 17.5-14S75 80 77 90z" fill="#fff"/></svg>
  <h3>ORLA<br>SECURITY</h3>
  <p>50% discount on new glasses, if your<br>child's graduation has changed</p>
</div>
<div class="guarantee abs" style="left:838px">
  <svg width="119" height="131" viewBox="0 0 119 131"><polygon points="59.5,0 119,33 119,98 59.5,131 0,98 0,33" fill="var(--gold)"/><path d="M38 65c7-10 14-14 21.5-14S74 55 81 65c-7 10-14 14-21.5 14S45 75 38 65z" fill="#fff"/><circle cx="59.5" cy="65" r="8" fill="var(--gold)"/><circle cx="59.5" cy="65" r="3.5" fill="#fff"/></svg>
  <h3>MANUFACTURER'S<br>WARRANTY</h3>
  <p>50% discount on new glasses, if your<br>child's graduation has changed</p>
</div>

<div class="wave abs" style="top:2120px;height:270px" role="img" aria-label="Flowing warm light streaks"></div>

<div class="ghost brands-ghost abs">OUR BRANDS</div>
<h2 class="section-title brands-title abs">OUR BRANDS</h2>
<div class="brand-box abs" style="left:96px">MARSHAL</div>
<div class="brand-box abs" style="left:354px">JANE ROWE</div>
<div class="brand-box abs" style="left:610px">VELLANO</div>
<div class="brand-box abs" style="left:868px">STRADA</div>

<footer>
  <div class="site-footer abs"></div>
  <div class="footer-name abs">ORLA</div>
  <nav class="footer-nav abs"><span>START</span><span>ABOUT US</span><span>PRODUCTS</span><span>APPOINTMENTS</span><span>ASSISTANCE</span><span>CONTACT</span><span>BLOG</span><span>STORE</span></nav>
  <p class="copyright abs">Copyright © 2018 &nbsp;| All Rights Reserved</p>
</footer>

</body>
</html>
```